Need Business Card for our Real Estate Business with Sales Executive's Picture

PANTONE 484 C ( RED)

PANTONE 2766 C ( BLUE

Industry/Entity Type

Real Estate

Contact Information for Business Card

Name, Mobile, email, & picture of Person
Agency Phone, address, Web address

Requirements
Must have
• Our Logo Colours, Agent Picture,

```html
<!DOCTYPE html>
<html lang="en">
<head>
<meta charset="utf-8">
<title>Corvale Real Estate – Business Card</title>
<link href="https://fonts.googleapis.com/css2?family=Open+Sans:ital,wght@0,400;0,600;0,700;1,700&display=swap" rel="stylesheet">
<style>
  :root {
    --page: #3a3a3c;
    --card: #1f1f21;
    --card-edge: #2a2a2c;
    --red: #a6322d;
    --blue: #1b2f6b;
    --white: #ffffff;
    --muted: #4a4a4d;
    --photo-a: #2c4f9e;
    --photo-b: #1f1f21;
  }
  * { box-sizing: border-box; margin: 0; padding: 0; }
  html, body { width: 799px; height: 1200px; overflow: hidden; }
  body {
    background: var(--page);
    font-family: "Open Sans", Arial, sans-serif;
    color: var(--white);
    position: relative;
  }
  .card {
    position: absolute;
    left: 60px;
    width: 680px;
    height: 389px;
    background: var(--card);
    border: 1px solid var(--card-edge);
    overflow: hidden;
  }
  .card--front { top: 110px; }
  .card--back { top: 700px; }

  /* Front */
  .front-mark {
    position: absolute;
    left: 0; right: 0; top: 140px;
    text-align: center;
    font-weight: 700;
    font-size: 58px;
    letter-spacing: 14px;
    color: var(--muted);
  }
  .front-web {
    position: absolute;
    left: 0; right: 0; bottom: 62px;
    display: flex;
    align-items: center;
    justify-content: center;
    gap: 18px;
    font-size: 17px;
    letter-spacing: 0.5px;
  }
  .front-web .rule {
    width: 60px; height: 3px;
    background: var(--red);
  }

  /* Back */
  .corner-dot {
    position: absolute;
    left: -22px; top: 14px;
    width: 44px; height: 44px;
    border-radius: 50%;
    background: var(--red);
  }
  .agent { position: absolute; left: 44px; top: 26px; }
  .agent-name { font-weight: 700; font-style: italic; font-size: 23px; line-height: 1.2; }
  .agent-title { color: var(--red); font-size: 13px; font-weight: 600; }
  .agent-photo {
    position: absolute;
    left: 0; top: 120px;
    width: 230px; height: 269px;
    background: linear-gradient(180deg, var(--photo-b) 0%, #3b4a72 55%, var(--photo-a) 100%);
  }
  .brand {
    position: absolute;
    left: 330px; top: 120px;
    display: flex; align-items: center; gap: 12px;
    font-weight: 600; font-size: 34px; letter-spacing: 9px;
  }
  .brand .square { width: 12px; height: 12px; background: var(--red); }
  .contact {
    position: absolute;
    left: 332px; top: 206px;
    font-size: 15px; line-height: 1.35;
  }
  .contact .address { margin-bottom: 6px; }
  .contact li { list-style: none; display: flex; align-items: center; gap: 10px; }
  .contact svg { width: 14px; height: 14px; fill: var(--red); flex: none; }
  .band-accent {
    position: absolute;
    left: 212px; bottom: 0;
    width: 60px; height: 52px;
    background: var(--red);
    border-top-left-radius: 18px;
  }
  .band {
    position: absolute;
    left: 240px; right: 0; bottom: 0;
    height: 62px;
    background: var(--blue);
    border-top-left-radius: 26px;
    display: flex; align-items: center;
    padding-left: 60px;
    font-size: 17px;
  }
</style>
</head>
<body>
  <section class="card card--front">
    <div class="front-mark">CORVALE</div>
    <div class="front-web"><span class="rule"></span>www.corvalerealestate.com<span class="rule"></span></div>
  </section>

  <section class="card card--back">
    <div class="corner-dot"></div>
    <div class="agent">
      <p class="agent-name">Marissa Delgado</p>
      <p class="agent-title">Managing Director</p>
    </div>
    <div class="agent-photo" role="img" aria-label="Portrait photo of the sales executive in a blue suit"></div>

    <div class="brand"><span class="square"></span>CORVALE</div>

    <div class="contact">
      <p class="address">418 Alder Park Rd #210,<br>Brookfield, CO 80431</p>
      <ul>
        <li><svg viewBox="0 0 24 24"><path d="M6.6 10.8a15 15 0 0 0 6.6 6.6l2.2-2.2a1 1 0 0 1 1-.25 11.4 11.4 0 0 0 3.6.57 1 1 0 0 1 1 1V20a1 1 0 0 1-1 1A17 17 0 0 1 3 4a1 1 0 0 1 1-1h3.5a1 1 0 0 1 1 1c0 1.25.2 2.45.57 3.57a1 1 0 0 1-.25 1z"/></svg>555.214.3087</li>
        <li><svg viewBox="0 0 24 24"><path d="M7 2h10a2 2 0 0 1 2 2v16a2 2 0 0 1-2 2H7a2 2 0 0 1-2-2V4a2 2 0 0 1 2-2zm0 3v12h10V5zm5 13.5a1 1 0 1 0 0 2 1 1 0 0 0 0-2z"/></svg>555-630-4419</li>
        <li><svg viewBox="0 0 24 24"><path d="M2 5h20v14H2zm2 2v.5l8 5 8-5V7zm0 2.8V17h16V9.8l-8 5z"/></svg>mdelgado@corvalerealestate.com</li>
      </ul>
    </div>

    <div class="band-accent"></div>
    <div class="band">www.corvalerealestate.com</div>
  </section>
</body>
</html>
```